Aquatic View

We need a web design for a new window cleaning company name Tidewell Glass Care. We are located in Grand Cayman, Cayman Islands. We are a small company, a team of husband and wife. Our services include residencial interior and exterior window cleaning and commercial. Extra services such as ceiling fans cleaning, mirrors, high dusting. Home cleaning services. Power washing. Explaining the service. We want a modern, beachy style with aquatic colors. We want to use our domain name "tidewellglasscare.ky". We want to portray a clean, modern and professional design.

Target Market(s)

Big Home owners

Industry/Entity Type

Cleaning Service

Contact Information for Business Card

Company Name: Tidewell Glass Care
Name: Desmond Farrowby owner/manager
Phone: 345-9170452
Email: desmond@tidewellglasscare.ky
Website: tidewellglasscare.ky
Address: P.O.Box 2486 GT, George Town, Grand Cayman KY1-1203 Cayman Islands

Number of Pages Required

2 page

Font styles to use
Sans Serif

Colors
0592cd
0455a3
33a6d7
85cae6
cadf82
abd036
fbf289

Requirements
Nice to have
• Pictures of an ocean view and palm trees from clear windows.
• https://quorvantel.com/bidlinker/
• Use the above for "free estimate".

```html
<!DOCTYPE html>
<html lang="en">
<head>
<meta charset="utf-8">
<title>Tidewell Glass Care</title>
<link href="https://fonts.googleapis.com/css2?family=Lato:ital,wght@0,400;0,700;0,900;1,400&display=swap" rel="stylesheet">
<style>
:root{
  --topbar:#4a4a4a;
  --ink:#333;
  --body:#666;
  --red:#c0111a;
  --blue:#0592cd;
  --blue-dark:#0455a3;
  --blue-mid:#33a6d7;
  --line:#d9d9d9;
  --footer:#2b2b2b;
}
*{box-sizing:border-box;margin:0;padding:0}
html,body{width:1200px;height:1071px;overflow:hidden}
body{font-family:'Lato',sans-serif;background:#fff;position:relative;color:var(--body)}
.abs{position:absolute}
.topbar{left:0;top:0;width:1200px;height:34px;background:var(--topbar)}
.topbar .phone{right:116px;top:5px;color:#fff;font-size:19px;font-weight:700;display:flex;align-items:center;gap:6px}
.header{left:0;top:34px;width:1200px;height:69px;background:#fff}
.brand{left:120px;top:52px;display:flex;align-items:center;gap:8px;font-size:19px;font-weight:900;color:var(--blue-dark)}
.brand .dot{width:26px;height:26px;border-radius:50%;background:var(--blue)}
.nav{top:62px;left:728px;display:flex;align-items:center;font-size:13px;font-weight:700;color:var(--ink);height:22px}
.nav a{text-decoration:none;color:inherit;padding:0 13px;line-height:22px}
.nav a.active{color:var(--blue);border:1px solid var(--blue);padding:0 12px}
.nav .sep{width:1px;height:16px;background:var(--line)}
.hero{left:0;top:103px;width:1200px;height:501px;background:linear-gradient(100deg,#6f7a5f 0%,#8c8d86 35%,#7d7f84 65%,#5c5d62 100%)}
.below{left:0;top:604px;width:1200px;height:318px;background:linear-gradient(#e4e4e4,#fff 80%)}
.tile{width:274px;height:274px;border-radius:50%;border:12px solid rgba(225,225,225,.85);overflow:hidden;top:223px}
.tile .ph{position:absolute;inset:0}
.tile .label{position:absolute;left:0;right:0;top:189px;height:72px;background:rgba(20,20,20,.75);color:#fff;font-size:22px;font-weight:700;text-align:center;padding-top:12px}
.arrow{width:36px;height:36px;border-radius:50%;background:#e6e6e6;top:333px;display:flex;align-items:center;justify-content:center;box-shadow:0 1px 3px rgba(0,0,0,.3)}
.panel{left:99px;top:573px;width:1002px;height:320px;background:#fff}
h2{position:absolute;top:598px;font-size:17px;font-weight:900;letter-spacing:.5px;color:var(--blue)}
h2 span{color:var(--red)}
.rule{position:absolute;top:629px;height:2px;background:var(--line)}
.rule i{display:block;width:85px;height:2px;background:var(--blue)}
.vdiv{top:613px;width:1px;height:257px;background:#ececec}
p{font-size:13px;line-height:19.5px;color:var(--body)}
.btn{background:linear-gradient(var(--blue),var(--blue-dark));color:#fff;font-size:13px;font-weight:700;display:flex;align-items:center;justify-content:center;height:31px}
.svc h3{font-size:15px;font-weight:700;color:var(--blue);position:absolute;left:460px}
.svc .ico{position:absolute;left:433px}
.svc p{position:absolute;left:462px;width:300px}
.field{left:817px;width:265px;border:1px solid #cfcfcf;font-size:12.5px;color:#666;padding:8px 6px}
.footer{left:0;top:922px;width:1200px;height:106px;background:var(--footer)}
.flinks{left:117px;top:941px;display:flex;font-size:13px;font-weight:700;color:#fff;gap:0}
.flinks span{margin-right:14px}
.finfo{font-size:13px;color:#fff;display:flex;align-items:center;gap:8px}
.sub{left:842px;top:941px;width:242px;height:30px;display:flex}
.sub .in{flex:1;background:#fff;font-size:11px;font-style:italic;color:#888;display:flex;align-items:center;gap:6px;padding-left:8px}
.sub .go{width:84px;background:var(--blue-dark);color:#fff;font-size:12.5px;font-weight:700;display:flex;align-items:center;justify-content:center}
.social{width:24px;height:24px;border-radius:50%;border:1.5px solid #fff;top:989px}
.copy{left:0;top:1028px;width:1200px;height:43px;background:linear-gradient(var(--blue),var(--blue-dark));color:#fff;font-size:13px;text-align:center;line-height:43px}
</style>
</head>
<body>
<div class="abs topbar">
  <div class="abs phone">
    <svg width="24" height="24" viewBox="0 0 24 24"><circle cx="12" cy="12" r="11" fill="none" stroke="#fff" stroke-width="1.5"/><path d="M8.5 6.5l2 2-1 1.5c.8 1.6 2 2.8 3.5 3.5l1.5-1 2 2-1.5 1.6c-3.5-.5-7-4-7.5-7.5z" fill="#fff"/></svg>
    345-9170452
  </div>
</div>
<div class="abs header"></div>
<div class="abs brand"><span class="dot"></span>Tidewell Glass Care</div>
<nav class="abs nav">
  <a class="active">HOME</a><a>ABOUT US</a><span class="sep"></span><a>SERIVCES</a><span class="sep"></span><a>CONTACT US</a>
</nav>

<div class="abs hero" role="img" aria-label="Photo of a worker cleaning a window with a squeegee pole"></div>

<div class="abs tile" style="left:143px"><div class="ph" role="img" aria-label="Residential window cleaning photo" style="background:linear-gradient(135deg,#c9d4d8,#8aa07a 55%,#dfe6ea)"></div><div class="label">RESIDENTIAL</div></div>
<div class="abs tile" style="left:463px"><div class="ph" role="img" aria-label="Commercial high-rise window cleaning photo" style="background:linear-gradient(135deg,#3b6fb8,#8fb6e2 50%,#3a63a6)"></div><div class="label">COMMERCIAL</div></div>
<div class="abs tile" style="left:782px"><div class="ph" role="img" aria-label="Floor cleaning equipment photo" style="background:linear-gradient(135deg,#7a7a72,#2f55b4 55%,#b8b8b2)"></div><div class="label">OTHER SERVICE</div></div>

<div class="abs arrow" style="left:33px"><svg width="12" height="14" viewBox="0 0 12 14"><path d="M9 1L3 7l6 6" fill="none" stroke="#555" stroke-width="3"/></svg></div>
<div class="abs arrow" style="left:1130px"><svg width="12" height="14" viewBox="0 0 12 14"><path d="M3 1l6 6-6 6" fill="none" stroke="#555" stroke-width="3"/></svg></div>

<div class="abs below"></div>
<div class="abs panel"></div>

<h2 style="left:117px"><span>ABOUT</span> TIDEWELL GLASS CARE</h2>
<div class="rule" style="left:116px;width:265px"><i></i></div>
<div class="abs" role="img" aria-label="Photo of a cleaner washing an exterior window" style="left:116px;top:644px;width:265px;height:122px;border:1px solid #bbb;background:linear-gradient(110deg,#dfe8f0,#5a86b8 45%,#c9d6de)"></div>
<p class="abs" style="left:117px;top:774px;width:266px">Lorem ipsum dolor sit amet, consectetuer adip iscing elit, sed diam nonummy nibh euismod magna aliquam erat volutpat.</p>
<div class="abs btn" style="left:116px;top:841px;width:94px">READ MORE</div>

<div class="abs vdiv" style="left:407px"></div>

<h2 style="left:433px"><span>OUR</span> SERVICES</h2>
<div class="rule" style="left:433px;width:334px"><i></i></div>
<div class="svc">
  <p style="left:434px;top:641px;width:330px">Lorem ipsum dolor sit amet, consectetuer adip iscing elit sed diam nonummy nibh euismod magna.</p>
  <svg class="ico" style="top:687px" width="20" height="17" viewBox="0 0 20 17"><path d="M10 1L1 8h3v8h5v-5h2v5h5V8h3z" fill="#777"/></svg>
  <h3 style="top:686px">Residential</h3>
  <p style="top:705px">Lorem ipsum dolor sit amet, consectetuer adip iscing elit sed diam nonummy nibh euismod magna.</p>
  <svg class="ico" style="top:749px" width="20" height="19" viewBox="0 0 20 19"><path d="M6 1h8v18H6zM1 7h5v12H1zM14 9h5v10h-5z" fill="#777"/><path d="M8 4h1.5v1.5H8zM10.5 4H12v1.5h-1.5zM8 8h1.5v1.5H8zM10.5 8H12v1.5h-1.5zM8 12h1.5v1.5H8zM10.5 12H12v1.5h-1.5z" fill="#fff"/></svg>
  <h3 style="top:749px">Commercial</h3>
  <p style="top:768px">Lorem ipsum dolor sit amet, consectetuer adip iscing elit sed diam nonummy nibh euismod magna.</p>
  <svg class="ico" style="top:816px" width="20" height="20" viewBox="0 0 20 20"><circle cx="7" cy="7" r="4.5" fill="none" stroke="#777" stroke-width="3" stroke-dasharray="2 1.5"/><circle cx="15" cy="15" r="3" fill="none" stroke="#777" stroke-width="2.5" stroke-dasharray="1.5 1.2"/></svg>
  <h3 style="top:816px">Extra Services</h3>
  <p style="top:837px">Lorem ipsum dolor sit amet, consectetuer adip iscing elit sed diam nonummy nibh euismod magna.</p>
</div>

<div class="abs vdiv" style="left:793px"></div>

<h2 style="left:819px"><span>QUICK</span> INQUIRY</h2>
<div class="rule" style="left:817px;width:265px"><i></i></div>
<div class="abs field" style="top:647px;height:30px">Email</div>
<div class="abs field" style="top:684px;height:30px">Phone</div>
<div class="abs field" style="top:722px;height:30px">Email</div>
<div class="abs field" style="top:759px;height:73px">Message</div>
<div class="abs btn" style="left:817px;top:841px;width:89px">SUBMIT</div>

<div class="abs footer"></div>
<div class="abs flinks"><span>Home</span><span>I</span><span>About Us</span><span>I</span><span>Serivces</span><span style="margin-right:14px">I</span><span>Contact Us</span></div>
<div class="abs finfo" style="left:117px;top:970px">
  <svg width="12" height="15" viewBox="0 0 12 15"><path d="M6 0a5 5 0 00-5 5c0 4 5 10 5 10s5-6 5-10a5 5 0 00-5-5z" fill="#ccc"/><circle cx="6" cy="5" r="2" fill="#2b2b2b"/></svg>
  Lorem ipsum dolor sit amet consectetuer adimpisciged
</div>
<div class="abs finfo" style="left:115px;top:994px">
  <svg width="16" height="16" viewBox="0 0 24 24"><circle cx="12" cy="12" r="11" fill="none" stroke="#ccc" stroke-width="1.5"/><path d="M8.5 6.5l2 2-1 1.5c.8 1.6 2 2.8 3.5 3.5l1.5-1 2 2-1.5 1.6c-3.5-.5-7-4-7.5-7.5z" fill="#ccc"/></svg>
  345-9170452
  <svg width="11" height="8" viewBox="0 0 11 8" style="margin-left:4px"><rect x=".5" y=".5" width="10" height="7" fill="none" stroke="#ccc"/><path d="M.5.5l5 4 5-4" fill="none" stroke="#ccc"/></svg>
  desmond@tidewellglasscare.ky
</div>
<div class="abs sub">
  <div class="in"><svg width="14" height="10" viewBox="0 0 14 10"><rect x=".5" y=".5" width="13" height="9" fill="none" stroke="#bbb"/><path d="M.5.5l6.5 5 6.5-5" fill="none" stroke="#bbb"/></svg>your e-mail address</div>
  <div class="go">SUBSCRIBE</div>
</div>
<div class="abs social" style="left:968px"></div>
<div class="abs social" style="left:1000px"></div>
<div class="abs social" style="left:1030px"></div>
<div class="abs social" style="left:1059px"></div>
<div class="abs copy">Copyright © 2015&nbsp; TidewellGlassCare. All Right Reserved</div>
</body>
</html>
```